BrindleStaffing Business Card Design

We are a staffing company finding positions for dedicated nurses and physicians.

Target Market(s)

Business Professionals

Industry/Entity Type

Staffing

Contact Information for Business Card

Gordon Pratley
Chairman
417 39th Avenue South
SAINT PETERSBURG FL 33712
813-555-4172 Mobile
813-555-8036 Fax
gpratley@brindlestaffing.com
www.brindlestaffing.com

Font styles to use
Sans Serif

Colors
fbee3e
f04a50
f37122

Requirements
Must have
• Logo Attached, see colors below. We'd like to see Yellow, Orange and Red.

```html
<!DOCTYPE html>
<html lang="en">
<head>
<meta charset="utf-8">
<title>BrindleStaffing Business Card</title>
<link rel="stylesheet" href="https://fonts.googleapis.com/css2?family=Roboto:wght@400;700&display=swap">
<style>
  :root {
    --brand-red: #f04a50;
    --brand-orange: #f37122;
    --brand-yellow: #fbee3e;
    --card-white: #ffffff;
    --backdrop: #e4e4e4;
    --text-on-red: #ffffff;
  }
  * { margin: 0; padding: 0; box-sizing: border-box; }
  html, body {
    width: 1125px;
    height: 1200px;
    overflow: hidden;
    background: var(--backdrop);
    font-family: "Roboto", Arial, sans-serif;
  }
  .card {
    position: absolute;
    left: 171px;
    width: 826px;
    height: 472px;
    border-radius: 24px;
    overflow: hidden;
    background: var(--card-white);
  }
  .card--front { top: 106px; }
  .card--back { top: 639px; background: var(--brand-red); }

  .card__shape { position: absolute; inset: 0; width: 100%; height: 100%; }

  .wordmark {
    position: absolute;
    left: 0; right: 0;
    display: flex;
    justify-content: center;
    align-items: center;
    gap: 14px;
    font-weight: 700;
    font-size: 70px;
    letter-spacing: -1.5px;
    line-height: 1;
  }
  .wordmark__dot {
    width: 24px; height: 24px;
    border-radius: 50%;
    flex: none;
    background: var(--brand-yellow);
  }
  .card--front .wordmark { top: 86px; color: var(--brand-red); }
  .card--front .wordmark__dot { background: var(--brand-orange); }
  .card--back .wordmark { top: 204px; color: var(--text-on-red); }

  .person {
    position: absolute;
    left: 0; right: 0;
    top: 218px;
    text-align: center;
  }
  .person__name {
    font-weight: 700;
    font-size: 35px;
    color: var(--brand-red);
    line-height: 1.05;
  }
  .person__role {
    font-weight: 700;
    font-size: 20px;
    color: var(--brand-orange);
    line-height: 1.1;
  }

  .contact {
    position: absolute;
    left: 0; right: 0;
    top: 359px;
    color: var(--text-on-red);
    font-size: 19px;
    line-height: 27px;
    text-align: center;
  }
  .contact__row {
    display: flex;
    justify-content: center;
    align-items: center;
    gap: 3px;
    white-space: nowrap;
  }
  .contact__item { display: inline-flex; align-items: center; gap: 3px; }
  .icon { width: 16px; height: 16px; fill: var(--text-on-red); flex: none; }

  .back__pattern { position: absolute; inset: 0; background: var(--brand-red); }
  .back__url {
    position: absolute;
    left: 0; right: 0;
    top: 406px;
    text-align: center;
    color: var(--text-on-red);
    font-size: 19px;
    letter-spacing: 6px;
  }
</style>
</head>
<body>

<section class="card card--front" aria-label="Business card front">
  <svg class="card__shape" viewBox="0 0 800 457" preserveAspectRatio="none" aria-hidden="true">
    <path d="M0 213 Q400 396 800 213 L800 457 L0 457 Z" fill="var(--brand-yellow)"/>
    <path d="M0 213 Q400 408 800 213 L800 457 L0 457 Z" fill="var(--card-white)"/>
    <path d="M0 213 Q400 412 800 213 L800 457 L0 457 Z" fill="var(--brand-red)"/>
  </svg>

  <div class="wordmark">
    <span class="wordmark__text">BrindleStaffing</span>
    <span class="wordmark__dot"></span>
  </div>

  <div class="person">
    <div class="person__name">Gordon Pratley</div>
    <div class="person__role">Chairman</div>
  </div>

  <div class="contact">
    <div class="contact__row">417 39th Avenue South, SAINT PETERSBURG FL 33712</div>
    <div class="contact__row">
      <span class="contact__item">
        <svg class="icon" viewBox="0 0 16 16" aria-hidden="true"><path d="M4 0h8a1.5 1.5 0 0 1 1.5 1.5v13A1.5 1.5 0 0 1 12 16H4a1.5 1.5 0 0 1-1.5-1.5v-13A1.5 1.5 0 0 1 4 0zm.5 2v10.5h7V2z"/></svg>813-555-4172
      </span>
      <span class="contact__item">
        <svg class="icon" viewBox="0 0 16 16" aria-hidden="true"><path d="M4 1h7l1 2v3H4zM1 7h14v6H1zm2 2v2h10V9zM4 14h8v1H4z"/></svg>813-555-8036
      </span>
      <span class="contact__item">
        <svg class="icon" viewBox="0 0 16 16" aria-hidden="true"><path d="M1 3h14v10H1zm1.2 1.2L8 8.6l5.8-4.4z"/></svg>gpratley@brindlestaffing.com
      </span>
    </div>
    <div class="contact__row">
      <span class="contact__item">
        <svg class="icon" viewBox="0 0 16 16" aria-hidden="true"><path d="M8 0.5a7.5 7.5 0 1 0 0 15 7.5 7.5 0 0 0 0-15zM4 4.5l2.5-1 1 2-2 2 1 2.5-1 2.5-2-2.5-1-3zm6 1.5 2 .5 1 3-2 2.5-1-2.5-1.5-1z"/></svg>&nbsp;www.brindlestaffing.com
      </span>
    </div>
  </div>
</section>

<section class="card card--back" aria-label="Business card back">
  <div class="back__pattern" role="img" aria-label="Red background with soft lighter dot pattern"></div>
  <div class="wordmark">
    <span class="wordmark__text">BrindleStaffing</span>
    <span class="wordmark__dot"></span>
  </div>
  <div class="back__url">www.brindlestaffing.com</div>
</section>

</body>
</html>
```